Resposive web site in 4 languages + image gallery + logo design

We need a web page, which will work on all devices.
I have uploaded web page concept.
Company name: Praxelun
Industry/Entity Type
It Company
Logo Text
quality matters
Coding
Coded - Design and coding required
Number of Pages Required
1 page

```html
<!DOCTYPE html>
<html lang="en">
<head>
<meta charset="utf-8">
<title>Praxelun — Woodworks</title>
<link href="https://fonts.googleapis.com/css2?family=Raleway:wght@400;500;600;700;800&display=swap" rel="stylesheet">
<style>
:root{
  --orange:#f7941d;
  --ink:#2b2b2b;
  --text:#555;
  --white:#fff;
  --dark:#2d2d2d;
  --field:#f4f4f4;
  --line:#dcdcdc;
  --wood-1:#3a1d0c;
  --wood-2:#5a2f14;
  --caption:rgba(20,16,12,.82);
}
*{margin:0;padding:0;box-sizing:border-box}
html,body{width:1200px;height:3797px;overflow:hidden}
body{position:relative;background:var(--white);font-family:"Raleway",sans-serif;color:var(--text)}
.abs{position:absolute}

/* header */
.site-header{left:0;top:0;width:1200px;height:84px;background:var(--white)}
.brand{left:76px;top:29px;font-size:26px;font-weight:800;color:var(--ink);letter-spacing:1px;text-transform:uppercase}
.nav a{position:absolute;top:36px;font-size:13px;font-weight:600;color:var(--ink);text-decoration:none;text-transform:uppercase}
.nav a.active{color:var(--orange)}
.social-dot{width:14px;height:14px;border-radius:50%;background:var(--ink);top:35px}
.lang{left:1066px;top:33px;font-size:13px;font-weight:600;color:var(--ink);display:flex;align-items:center;gap:6px}

/* hero */
.hero{left:0;top:84px;width:1200px;height:569px;background:radial-gradient(ellipse at 50% 45%,#6b4a32 0%,#4a2f1e 55%,#2c1b11 100%)}
.hero-title{left:0;width:1200px;top:250px;text-align:center;font-size:84px;font-weight:700;color:var(--white);letter-spacing:1px}
.hero-sub{left:0;width:1200px;top:342px;text-align:center;font-size:40px;font-weight:500;color:var(--white)}
.btn-quote{left:491px;top:420px;width:218px;height:53px;background:var(--orange);color:var(--white);font-size:22px;font-weight:700;display:flex;align-items:center;justify-content:center;text-transform:uppercase}

/* section headings */
.section-title{left:0;width:1200px;text-align:center;font-size:50px;font-weight:700;color:var(--ink);text-transform:uppercase}
.title-rule{left:570px;width:60px;height:3px;background:var(--ink)}

/* service blocks */
.service-title{font-size:27px;font-weight:700;color:var(--ink);text-transform:uppercase}
.service-text{font-size:15px;line-height:25px;width:600px}
.service-text p+p{margin-top:6px}
.photo{overflow:hidden}
.caption{position:absolute;left:0;width:100%;height:72px;background:var(--caption);display:flex;align-items:center;justify-content:space-between;padding:0 18px}
.caption span{font-size:24px;font-weight:700;color:var(--orange)}
.wood-band{left:0;top:1286px;width:1200px;height:601px}
.on-dark .service-title,.on-dark .service-text{color:var(--white)}

/* about */
.about-photo{left:0;top:2443px;width:587px;height:626px;background:linear-gradient(135deg,#c9b8a4 0%,#8d6e55 50%,#5b4636 100%)}
.about-title{left:633px;top:2510px;font-size:50px;font-weight:700;color:var(--white)}
.about-text{left:633px;top:2600px;width:500px;font-size:15px;line-height:25px;color:var(--white)}
.about-text p+p{margin-top:8px}
.about-sign{left:633px;top:2902px;color:var(--white);font-size:15px;line-height:25px}
.about-sign strong{font-size:18px;font-weight:700}

/* contact */
.contact-sub{left:0;width:1200px;top:3214px;text-align:center;font-size:22px;color:#444}
.col-title{font-size:21px;font-weight:600;color:var(--ink);text-transform:uppercase}
.info{left:76px;top:3362px;font-size:14px;line-height:22px;color:var(--text)}
.info .name{font-size:17px;font-weight:700;color:var(--ink)}
.info-row{display:flex;align-items:center;gap:12px;margin-top:12px}
.info a{display:block;margin-top:12px;color:var(--ink);font-weight:700;text-decoration:none}
.field{background:var(--field);border:1px solid var(--line);font-size:13px;color:#888;padding:0 12px;display:flex;align-items:center}
.field.area{align-items:flex-start;padding-top:12px}
.btn-send{left:1013px;top:3532px;width:114px;height:38px;background:var(--dark);color:var(--white);font-size:13px;font-weight:700;display:flex;align-items:center;justify-content:center}

/* footer */
.site-footer{left:0;top:3626px;width:1200px;height:171px;background:var(--dark);color:var(--white)}
.foot-nav{left:0;width:1200px;top:30px;display:flex;justify-content:center;gap:70px;font-size:13px;font-weight:700;text-transform:uppercase}
.foot-copy{left:0;width:1200px;top:66px;text-align:center;font-size:12px;line-height:24px;color:#bbb}
.foot-social{left:0;width:1200px;top:125px;display:flex;justify-content:center;gap:24px}
.foot-social i{width:16px;height:16px;border-radius:50%;background:var(--white);display:block}
</style>
</head>
<body>

<header class="abs site-header">
  <div class="abs brand">Praxelun</div>
  <nav class="nav">
    <a class="active" style="left:466px">Home</a>
    <a style="left:568px">Services</a>
    <a style="left:692px">About us</a>
    <a style="left:822px">Contact</a>
  </nav>
  <span class="abs social-dot" style="left:968px" aria-label="Social link"></span>
  <span class="abs social-dot" style="left:1006px" aria-label="Social link"></span>
  <div class="abs lang">
    <svg width="16" height="16" viewBox="0 0 16 16"><circle cx="8" cy="8" r="7" fill="none" stroke="#2b2b2b" stroke-width="1.6"/><path d="M1 8h14M8 1c3 3.5 3 10.5 0 14M8 1c-3 3.5-3 10.5 0 14" fill="none" stroke="#2b2b2b" stroke-width="1.2"/></svg>
    EN
    <svg width="9" height="6" viewBox="0 0 9 6"><path d="M1 1l3.5 3.5L8 1" fill="none" stroke="#2b2b2b" stroke-width="1.4"/></svg>
  </div>
</header>

<section class="abs hero" role="img" aria-label="Carpentry tools laid out on a wooden workbench">
</section>
<svg class="abs" style="left:60px;top:330px" width="44" height="80" viewBox="0 0 44 80"><path d="M38 4L6 40l32 36" fill="none" stroke="#fff" stroke-width="4" opacity=".85"/></svg>
<svg class="abs" style="left:1096px;top:330px" width="44" height="80" viewBox="0 0 44 80"><path d="M6 4l32 36L6 76" fill="none" stroke="#fff" stroke-width="4" opacity=".85"/></svg>
<h1 class="abs hero-title">WOODWORKS</h1>
<p class="abs hero-sub">Are you interested in an estimate?</p>
<div class="abs btn-quote">Get a quote</div>
<svg class="abs" style="left:588px;top:578px" width="24" height="30" viewBox="0 0 24 30"><rect x="3" y="2" width="18" height="26" rx="9" fill="none" stroke="#fff" stroke-width="2"/><rect x="10.5" y="8" width="3" height="7" rx="1.5" fill="#fff"/></svg>

<h2 class="abs section-title" style="top:696px">Our services</h2>
<div class="abs title-rule" style="top:766px"></div>

<!-- wood works -->
<h3 class="abs service-title" style="left:76px;top:914px">Wood works</h3>
<div class="abs service-text" style="left:76px;top:968px">
  <p>Timber is, in essence, a natural and warm material. Wood is also relatively durable and easy to work with, which has made it a favourite of builders throughout history.</p>
  <p>Our goal is to offer suitable products and quality furniture with installation and after-sales service to all of our clients. In order to achieve this, we're ready to help our clients in all stages of construction from design to production and maintenance.</p>
</div>
<div class="abs photo" style="left:704px;top:813px;width:423px;height:461px;background:linear-gradient(120deg,#c9a27a 0%,#a9743f 55%,#6e3b1c 100%)" role="img" aria-label="Craftsman fitting a wooden cabinet door">
  <div class="caption" style="top:196px">
    <svg width="20" height="20" viewBox="0 0 20 20"><circle cx="10" cy="10" r="8" fill="none" stroke="#fff" stroke-width="2"/><path d="M11.5 6.5L8 10l3.5 3.5" fill="none" stroke="#fff" stroke-width="2"/></svg>
    <span>Furniture</span>
    <svg width="20" height="20" viewBox="0 0 20 20"><circle cx="10" cy="10" r="8" fill="none" stroke="#fff" stroke-width="2"/><path d="M8.5 6.5L12 10l-3.5 3.5" fill="none" stroke="#fff" stroke-width="2"/></svg>
  </div>
</div>

<!-- stone works band -->
<svg class="abs wood-band" viewBox="0 0 1200 601" role="img" aria-label="Dark wood grain background">
  <defs><linearGradient id="woodGrad" x1="0" y1="0" x2="1" y2="0"><stop offset="0" stop-color="#3a1d0c"/><stop offset=".5" stop-color="#5a2f14"/><stop offset="1" stop-color="#3b1c0b"/></linearGradient></defs>
  <polygon points="0,69 1200,0 1200,601 0,537" fill="url(#woodGrad)"/>
</svg>
<div class="abs photo" style="left:76px;top:1362px;width:418px;height:461px;background:linear-gradient(160deg,#e8d8be 0%,#c79a63 50%,#8a5a2e 100%)" role="img" aria-label="Bathroom with stone tiled wall and white sink">
  <div class="caption" style="top:196px">
    <svg width="20" height="20" viewBox="0 0 20 20"><circle cx="10" cy="10" r="8" fill="none" stroke="#fff" stroke-width="2"/><path d="M11.5 6.5L8 10l3.5 3.5" fill="none" stroke="#fff" stroke-width="2"/></svg>
    <span>Walls</span>
    <svg width="20" height="20" viewBox="0 0 20 20"><circle cx="10" cy="10" r="8" fill="none" stroke="#fff" stroke-width="2"/><path d="M8.5 6.5L12 10l-3.5 3.5" fill="none" stroke="#fff" stroke-width="2"/></svg>
  </div>
</div>
<div class="on-dark">
  <h3 class="abs service-title" style="left:527px;top:1482px">Stone works</h3>
  <div class="abs service-text" style="left:527px;top:1536px;width:600px">
    <p>The natural stone found in the ground has been used in construction for centuries because of its durability. A structure built by a skilled craftsman from natural stone is unique, genuine durable, and perfect for our bracing climate.</p>
    <p>Our experienced craftsmen are ready to help you in all stages of construction from planning to completion.</p>
  </div>
</div>

<!-- restoration -->
<h3 class="abs service-title" style="left:76px;top:2024px">Restoration</h3>
<div class="abs service-text" style="left:76px;top:2078px">
  <p>It's good to see that fixing old things has become popular again in recent years and people are trying to find ways to preserve GALLERY (sliders)valuable old windows and pieces of furniture before deciding to.</p>
  <p>It is possible to give a new life to almost any wooden door, window, piece of furniture or staircase. The extensive experience of our craftsmen will help you achieve the desired result.</p>
</div>
<div class="abs photo" style="left:704px;top:1924px;width:423px;height:461px;background:radial-gradient(ellipse at 40% 30%,#d9782a 0%,#8a4416 45%,#3a1a08 100%)" role="img" aria-label="Hand sanding a wooden board">
  <div class="caption" style="top:196px">
    <svg width="20" height="20" viewBox="0 0 20 20"><circle cx="10" cy="10" r="8" fill="none" stroke="#fff" stroke-width="2"/><path d="M11.5 6.5L8 10l3.5 3.5" fill="none" stroke="#fff" stroke-width="2"/></svg>
    <span>Furniture</span>
    <svg width="20" height="20" viewBox="0 0 20 20"><circle cx="10" cy="10" r="8" fill="none" stroke="#fff" stroke-width="2"/><path d="M8.5 6.5L12 10l-3.5 3.5" fill="none" stroke="#fff" stroke-width="2"/></svg>
  </div>
</div>

<!-- about -->
<svg class="abs" style="left:0;top:2393px" width="1200" height="676" viewBox="0 0 1200 676">
  <polygon points="587,50 1200,0 1200,676 587,676" fill="#f7941d"/>
</svg>
<div class="abs about-photo" role="img" aria-label="Carpenter with safety glasses and ear protection working on a plank"></div>
<h2 class="abs about-title">ABOUT US</h2>
<div class="abs about-text">
  <p>Praxelun is a company whose business operations include making wooden products, restoration and building structures from natural stone.</p>
  <p>All of our products are made by craftsmen and specialists who have extensive experience and knowledge in their fields.</p>
  <p>The products we offer are always handmade and we take the requests and ideas of the specific client into account. We always strive to achieve the best possible quality.</p>
</div>
<div class="abs about-sign"><strong>Quality matters,</strong><br>Praxelun</div>

<!-- contact -->
<h2 class="abs section-title" style="top:3116px">Contact us</h2>
<div class="abs title-rule" style="top:3183px"></div>
<p class="abs contact-sub">Contact Please Fill In The Following Fields If You Would Like A Price Quote</p>

<h4 class="abs col-title" style="left:76px;top:3304px">Contact info</h4>
<div class="abs info">
  <div class="name">Praxelun</div>
  <div>Lindra 12 10115</div>
  <div>Kaarlin</div>
  <div class="info-row">
    <svg width="14" height="14" viewBox="0 0 14 14"><path d="M3 1l2.5 3-1.5 1.5c.8 1.8 2 3 3.5 3.5L9 7.5l3 2.5-1.5 2.5C6 12 2 8 1.5 3z" fill="#2b2b2b"/></svg>
    Telephone: +000 55 01234
  </div>
  <div class="info-row" style="margin-top:4px">
    <svg width="14" height="12" viewBox="0 0 14 12"><rect x="0.5" y="0.5" width="13" height="11" fill="#2b2b2b"/><path d="M1 1l6 5 6-5" fill="none" stroke="#fff" stroke-width="1.2"/></svg>
    E-mail: info@praxelun.com
  </div>
  <a>Get Directions</a>
</div>

<h4 class="abs col-title" style="left:435px;top:3304px">Quick contact</h4>
<div class="abs field" style="left:435px;top:3368px;width:337px;height:38px">Name</div>
<div class="abs field" style="left:435px;top:3426px;width:337px;height:38px">Email Address</div>
<div class="abs field" style="left:435px;top:3484px;width:337px;height:38px">Phone No.</div>
<div class="abs field area" style="left:787px;top:3368px;width:340px;height:148px">Message</div>
<div class="abs btn-send">SEND</div>

<footer class="abs site-footer">
  <nav class="abs foot-nav"><span>Home</span><span>Services</span><span>About us</span><span>Contact</span></nav>
  <div class="abs foot-copy">Copyright © 2018 Company Name All Right Reserved<br>Privacy Policy &nbsp;|&nbsp; Terms of Services</div>
  <div class="abs foot-social"><i aria-label="Social link"></i><i aria-label="Social link"></i></div>
</footer>

</body>
</html>
```